Need Business Card for our Real Estate Business with Sales Executive's Picture

PANTONE 484 C ( RED)

PANTONE 2766 C ( BLUE

Industry/Entity Type

Real Estate

Contact Information for Business Card

Name, Mobile, email, & picture of Person
Agency Phone, address, Web address

Requirements
Must have
• Our Logo Colours, Agent Picture,

```html
<!DOCTYPE html>
<html lang="en">
<head>
<meta charset="utf-8">
<title>Meridian Real Estate – Business Card</title>
<link href="https://fonts.googleapis.com/css2?family=Open+Sans:wght@400;600;700&display=swap" rel="stylesheet">
<style>
  :root {
    --navy: #17265c;
    --red: #a3282b;
    --white: #ffffff;
    --paper: #e6e6e8;
    --ink-soft: #d9def0;
  }
  * { box-sizing: border-box; margin: 0; padding: 0; }
  html, body { width: 1200px; height: 852px; overflow: hidden; }
  body {
    background: var(--paper);
    font-family: "Open Sans", Arial, sans-serif;
    position: relative;
  }
  .card {
    position: absolute;
    width: 520px;
    height: 300px;
    border-radius: 22px;
    overflow: hidden;
    box-shadow: 0 6px 16px rgba(0,0,0,0.18);
  }

  /* Shared wordmark: one font, one weight, one colour */
  .wordmark {
    display: flex;
    align-items: center;
    gap: 10px;
    font-family: "Open Sans", Arial, sans-serif;
    font-weight: 600;
    letter-spacing: 1px;
    line-height: 1;
    white-space: nowrap;
  }
  .wordmark-square {
    flex: none;
    background: var(--red);
  }

  /* Brand side */
  .card-brand {
    left: 60px; top: 130px;
    background: var(--navy);
    color: var(--white);
  }
  .card-brand .wordmark {
    position: absolute;
    left: 0; right: 0; top: 128px;
    justify-content: center;
    font-size: 32px;
  }
  .card-brand .wordmark-square { width: 14px; height: 14px; }
  .brand-web {
    position: absolute;
    left: 0; right: 0; top: 218px;
    text-align: center;
    font-size: 13px;
    letter-spacing: 0.3px;
  }
  .brand-accent {
    position: absolute;
    left: 0; top: 0;
    width: 520px; height: 300px;
  }

  /* Contact side */
  .card-contact {
    left: 620px; top: 420px;
    background: var(--white);
  }
  .contact-waves { position: absolute; inset: 0; }
  .card-contact .wordmark {
    position: absolute;
    left: 96px; top: 34px;
    color: var(--navy);
    font-size: 22px;
  }
  .card-contact .wordmark-square { width: 10px; height: 10px; }
  .agent {
    position: absolute;
    left: 34px; top: 88px;
  }
  .agent-name {
    color: var(--navy);
    font-weight: 700;
    font-size: 19px;
    line-height: 1.2;
  }
  .agent-title {
    color: var(--red);
    font-size: 13px;
    line-height: 1.3;
  }
  .agent-photo {
    position: absolute;
    right: 14px; top: 80px;
    width: 150px; height: 220px;
    background: linear-gradient(180deg, #c79a83 0%, #b0836c 38%, #2d4690 62%, #1b2d6b 100%);
    border-radius: 70px 70px 0 0;
  }
  .contact-list {
    position: absolute;
    left: 34px; bottom: 14px;
    list-style: none;
    color: var(--white);
    font-size: 13px;
    line-height: 19px;
  }
  .contact-list li { display: flex; align-items: center; gap: 9px; }
  .contact-list svg { width: 12px; height: 12px; flex: none; fill: var(--ink-soft); }
</style>
</head>
<body>

  <section class="card card-brand">
    <svg class="brand-accent" viewBox="0 0 520 300" aria-hidden="true">
      <path d="M470 196 L520 180 L520 184 L470 200 Z" fill="var(--red)"/>
      <path d="M40 268 L110 250 L110 254 L40 272 Z" fill="var(--red)"/>
    </svg>
    <div class="wordmark"><span class="wordmark-square"></span>MERIDIAN REAL ESTATE</div>
    <div class="brand-web">www.meridianrealestate.com</div>
  </section>

  <section class="card card-contact">
    <svg class="contact-waves" viewBox="0 0 520 300" aria-hidden="true">
      <path d="M0 184 C150 150 330 160 520 70 L520 300 L0 300 Z" fill="var(--navy)"/>
      <path d="M0 172 C150 138 330 148 520 58" fill="none" stroke="var(--red)" stroke-width="7"/>
      <path d="M0 106 A22 22 0 0 1 0 150 Z" fill="var(--red)"/>
    </svg>

    <div class="wordmark"><span class="wordmark-square"></span>MERIDIAN REAL ESTATE</div>

    <div class="agent">
      <div class="agent-name">Laura Whitfield</div>
      <div class="agent-title">Managing Director</div>
    </div>

    <div class="agent-photo" role="img" aria-label="Portrait photo of the sales executive in a navy suit"></div>

    <ul class="contact-list">
      <li><svg viewBox="0 0 12 12"><rect x="3" y="0.5" width="6" height="11" rx="1.2"/></svg>555.210.4471</li>
      <li><svg viewBox="0 0 12 12"><path d="M2.5 1 L4.5 1 L5.5 3.8 L4.2 4.8 C5 6.5 5.5 7 7.2 7.8 L8.2 6.5 L11 7.5 L11 9.5 C11 10.5 10 11 9 11 C4.5 10.5 1.5 7.5 1 3 C1 2 1.5 1 2.5 1 Z"/></svg>555-386-9024</li>
      <li><svg viewBox="0 0 12 12"><rect x="1" y="1" width="10" height="10" rx="1"/></svg>meridianrealestate.com</li>
      <li><svg viewBox="0 0 12 12"><path d="M0.5 2.5 H11.5 V9.5 H0.5 Z M1 3 L6 7 L11 3"/></svg>lwhitfield@meridianrealestate.com</li>
      <li><svg viewBox="0 0 12 12"><circle cx="6" cy="6" r="5.5"/></svg>418 Aspen Ridge Dr #210, Fairview, CO 80451</li>
    </ul>
  </section>

</body>
</html>
```